Very visible CoWorking Building Sign overlooking downtown LA and 110 freeway

Our building is drab but very visible and in the best location. We need a great sign for our monolith that overlooks downtown LA and the 100 freeway. We are a new CoWorking business and would like to have a few things we do on the sign: private offices, virtual offices, CoWorking Lounge. Everything we have seen is ho-hum. Can you get us noticed? We need people to know what we do and that we are here but in a creative, professional, unique sign.
Target Market(s)
People who have a business in DTLA, remote workers and those who work from home who need a professional address.
Requirements
Must have
- Our logo (which can be somewhat reimagined) which has our address 2417 on it. The three things we focus on: Private Offices, Virtual Offices, CoWorking Lounge. Incorporate some Navy. Readable from several hundred feet away.
Nice to have
- Mural feel? Something inspirational in this crazy COVID times? Graphics? Color block. I like the idea of decorative but it has to be readable as a building sign. The same with the use of colors. Our colors are grays and navy but with a pop of the chartreuse (we have 2 velvet chartreuse chairs in the space). Helpful to view our website: Harborview2417.com.
Should not have
- Not too graffiti. Keep it professional but unique and wow.

```html
<!DOCTYPE html>
<html lang="en">
<head>
<meta charset="utf-8">
<title>Harborview2417 Building Sign</title>
<link href="https://fonts.googleapis.com/css2?family=Libre+Baskerville:wght@700&display=swap" rel="stylesheet">
<style>
  :root {
    --navy: #0d2548;
    --royal: #0a63ad;
    --chartreuse: #8dc63f;
    --white: #ffffff;
    --backdrop: #c4c4c4;
  }
  * { margin: 0; padding: 0; box-sizing: border-box; }
  html, body {
    width: 1200px;
    height: 1097px;
    overflow: hidden;
    background: var(--backdrop);
  }
  .sign {
    position: absolute;
    left: 300px;
    top: 48px;
    width: 600px;
    height: 1000px;
    background: var(--navy);
    color: var(--white);
    font-family: "Libre Baskerville", "Times New Roman", serif;
    font-weight: 700;
    overflow: hidden;
  }
  .sign-url {
    position: absolute;
    top: 68px;
    left: 0;
    width: 100%;
    text-align: center;
    font-size: 48px;
    letter-spacing: -0.5px;
  }
  .url-rule {
    position: absolute;
    top: 149px;
    left: 245px;
    width: 110px;
    height: 7px;
    background: var(--chartreuse);
  }
  .service {
    position: absolute;
    left: 49px;
    display: flex;
    align-items: center;
  }
  .service-icon {
    width: 142px;
    height: 142px;
    border-radius: 50%;
    background: var(--chartreuse);
    border: 2px solid var(--white);
    flex-shrink: 0;
  }
  .service-name {
    margin-left: 40px;
    font-size: 40px;
    line-height: 1.08;
    text-transform: uppercase;
    letter-spacing: 0.5px;
  }
  .service--private { top: 210px; }
  .service--virtual { top: 412px; }
  .service--lounge { top: 614px; }
  .divider {
    position: absolute;
    left: 230px;
    width: 183px;
    height: 1.5px;
    background: var(--white);
  }
  .divider--one { top: 381px; }
  .divider--two { top: 586px; }
  .footer-wave {
    position: absolute;
    left: 0;
    top: 753px;
    width: 600px;
    height: 247px;
  }
  .sign-phone {
    position: absolute;
    left: 0;
    top: 857px;
    width: 100%;
    text-align: center;
    font-size: 84px;
    letter-spacing: -3px;
    transform: scaleX(0.88);
  }
</style>
</head>
<body>
  <main class="sign">
    <h1 class="sign-url">Harborview2417.com</h1>
    <div class="url-rule"></div>

    <section class="service service--private">
      <div class="service-icon" role="img" aria-label="Line icon of a desk with chair, lamp and picture frame"></div>
      <h2 class="service-name">Private<br>Offices</h2>
    </section>
    <div class="divider divider--one"></div>

    <section class="service service--virtual">
      <div class="service-icon" role="img" aria-label="Line icon of a reception desk with mail and a plant"></div>
      <h2 class="service-name">Virtual<br>Offices</h2>
    </section>
    <div class="divider divider--two"></div>

    <section class="service service--lounge">
      <div class="service-icon" role="img" aria-label="Line icon of two people talking at a shared table"></div>
      <h2 class="service-name">Coworking<br>Lounge</h2>
    </section>

    <svg class="footer-wave" viewBox="0 0 600 247" preserveAspectRatio="none" aria-hidden="true">
      <path d="M0 0 C70 40 160 70 240 80 C150 80 60 55 0 38 Z" fill="var(--chartreuse)"/>
      <path d="M330 82 C420 70 520 50 600 40 V80 C520 70 430 78 330 82 Z" fill="var(--chartreuse)"/>
      <path d="M0 12 C120 70 260 95 380 75 C460 62 540 40 600 25 V36 C540 50 460 72 380 85 C260 105 120 82 0 22 Z" fill="var(--white)"/>
      <path d="M0 40 C120 90 250 100 360 88 C450 80 530 70 600 70 V247 H0 Z" fill="var(--royal)"/>
    </svg>

    <p class="sign-phone">310.555.2417</p>
  </main>
</body>
</html>
```